Carpentry framing business card and logo design

We need a logo that works well with baseball caps, tee shirts and sweat shirts. We are a carpentry framing company specializing in apartment complexes and large residential communities. We work in what is known as the tri state area southeastern Pennsylvania , New Jersey and northern Delaware . We would like to see die signs using the old English letter M and royal blue colors. Also we stress Jobsite compliance and safety.

Industry/Entity Type

Residential

Contact Information for Business Card

Valdrick Construction Co Inc
4870 Quillford Lane
Ambler PA 19087
Dale Valdrick
dale1valdrick@norvexmail.com
267-815-0926

```html
<!DOCTYPE html>
<html lang="en">
<head>
<meta charset="utf-8">
<title>Valdrick Construction – Business Card Options</title>
<link rel="stylesheet" href="https://fonts.googleapis.com/css2?family=Jost:wght@400;500;700&display=swap">
<style>
  :root {
    --page-bg: #e4e2dd;
    --card-bg: #f4f2ed;
    --ink-navy: #1f2d6e;
    --card-shadow: rgba(0, 0, 0, 0.12);
  }
  * { box-sizing: border-box; margin: 0; padding: 0; }
  html, body {
    width: 1029px;
    height: 1200px;
    overflow: hidden;
    background: var(--page-bg);
    font-family: "Jost", sans-serif;
    color: var(--ink-navy);
  }
  .sheet {
    width: 1029px;
    height: 1200px;
    padding: 34px;
    display: flex;
    flex-direction: column;
    gap: 34px;
  }
  .business-card {
    position: relative;
    width: 961px;
    height: 549px;
    background: var(--card-bg);
    box-shadow: 0 4px 14px var(--card-shadow);
  }
  .brand-block {
    position: absolute;
    left: 60px;
    top: 0;
    width: 340px;
    height: 100%;
    display: flex;
    flex-direction: column;
    align-items: center;
    justify-content: center;
  }
  .brand-name {
    font-weight: 500;
    font-size: 46px;
    letter-spacing: 1px;
    line-height: 1;
  }
  .brand-sub {
    font-weight: 500;
    font-size: 17px;
    letter-spacing: 3px;
    margin-top: 8px;
  }
  .divider {
    position: absolute;
    left: 420px;
    top: 140px;
    width: 2px;
    height: 270px;
    background: var(--ink-navy);
  }
  .contact-block {
    position: absolute;
    top: 150px;
  }
  .contact-block--left { left: 480px; text-align: left; }
  .contact-block--right { right: 90px; text-align: right; }
  .person-name {
    font-weight: 700;
    font-size: 44px;
    line-height: 1.1;
    margin-bottom: 14px;
  }
  .address {
    font-size: 17px;
    line-height: 1.2;
    margin-bottom: 18px;
  }
  .contact-line {
    display: flex;
    align-items: center;
    gap: 10px;
    font-size: 17px;
    line-height: 1.5;
  }
  .contact-block--right .contact-line { justify-content: flex-end; }
  .contact-block--right .address { margin-bottom: 14px; }
  .icon { width: 16px; height: 16px; flex: none; }
  .tagline {
    position: absolute;
    right: 80px;
    bottom: 60px;
    font-size: 17px;
    letter-spacing: 0.3px;
  }
</style>
</head>
<body>
<main class="sheet">

  <section class="business-card" aria-label="Business card, left-aligned contact layout">
    <div class="brand-block">
      <span class="brand-name">VALDRICK</span>
      <span class="brand-sub">CONSTRUCTION</span>
    </div>
    <div class="divider"></div>
    <div class="contact-block contact-block--left">
      <h1 class="person-name">Dale Valdrick</h1>
      <p class="address">4870 Quillford Lane<br>Harwick Vale QL 19087</p>
      <p class="contact-line">
        <svg class="icon" viewBox="0 0 16 16" aria-hidden="true"><rect x="1.5" y="3.5" width="13" height="9" fill="none" stroke="currentColor" stroke-width="1.4"/><path d="M1.5 3.5 L8 9 L14.5 3.5" fill="none" stroke="currentColor" stroke-width="1.4"/></svg>
        dale1valdrick@norvexmail.com
      </p>
      <p class="contact-line">
        <svg class="icon" viewBox="0 0 16 16" aria-hidden="true"><rect x="4" y="1.5" width="8" height="13" rx="1.5" fill="none" stroke="currentColor" stroke-width="1.4"/><line x1="7" y1="12" x2="9" y2="12" stroke="currentColor" stroke-width="1.4"/></svg>
        267-815-0926
      </p>
    </div>
    <p class="tagline">Jobsite compliance and SAFETY 1st</p>
  </section>

  <section class="business-card" aria-label="Business card, right-aligned contact layout">
    <div class="brand-block">
      <span class="brand-name">VALDRICK</span>
      <span class="brand-sub">CONSTRUCTION</span>
    </div>
    <div class="divider"></div>
    <div class="contact-block contact-block--right">
      <h2 class="person-name">Dale Valdrick</h2>
      <p class="address">4870 Quillford Lane<br>Harwick Vale QL 19087</p>
      <p class="contact-line">
        dale1valdrick@norvexmail.com
        <svg class="icon" viewBox="0 0 16 16" aria-hidden="true"><rect x="1.5" y="3.5" width="13" height="9" fill="none" stroke="currentColor" stroke-width="1.4"/><path d="M1.5 3.5 L8 9 L14.5 3.5" fill="none" stroke="currentColor" stroke-width="1.4"/></svg>
      </p>
      <p class="contact-line">
        267-815-0926
        <svg class="icon" viewBox="0 0 16 16" aria-hidden="true"><rect x="4" y="1.5" width="8" height="13" rx="1.5" fill="none" stroke="currentColor" stroke-width="1.4"/><line x1="7" y1="12" x2="9" y2="12" stroke="currentColor" stroke-width="1.4"/></svg>
      </p>
    </div>
    <p class="tagline">Jobsite compliance and SAFETY 1st</p>
  </section>

</main>
</body>
</html>
```